KIRO Nature Soap

We need to design new product Nature and medicative Soap.Made in Malaysia
* 100% natural.
* made from nature Tropic oil.
* Very effective for Acne & Skin irritation
* size 100 Gm.
* Use for all skin types including sensitive skin
* Name of the product " KIRO Soap"

Reason: please I need to extended since I haven't receive any suitable design for my project

Target Market(s)

International

Industry/Entity Type

Hair And Beauty

Font styles to use
Serif

Colors
33a6d7
abd037
fbed22

Requirements
Must have
• * must have English- Arabic ingredient
• * Very effective for Acne & Skin irritation
Nice to have
• * some things related to natural (water,tree,face..)
• * Show faces picture (after - before)

```html
<!DOCTYPE html>
<html lang="en">
<head>
<meta charset="utf-8">
<title>KIRO Soap – Packaging</title>
<link rel="stylesheet" href="https://fonts.googleapis.com/css2?family=Cinzel:wght@500;700&family=Tinos&display=swap">
<style>
  :root {
    --page-bg: #ececec;
    --cream: #f2efdc;
    --pattern-light: #d6e6a0;
    --pattern-mid: #a9cf52;
    --leaf-green: #8cc63f;
    --lime: #c9e04c;
    --band-green: #4e9c3a;
    --deep-green: #1d5414;
    --ink-green: #24420f;
    --white: #ffffff;
  }
  * { margin: 0; padding: 0; box-sizing: border-box; }
  html, body { width: 1200px; height: 1000px; overflow: hidden; background: var(--page-bg); }
  .canvas { position: relative; width: 1200px; height: 1000px; }

  /* End panel */
  .end-panel {
    position: absolute; left: 60px; top: 80px; width: 190px; height: 500px;
    background: linear-gradient(180deg, var(--lime), var(--leaf-green));
    display: flex; align-items: center; justify-content: center;
  }
  .end-panel .brand-name { transform: rotate(90deg); white-space: nowrap; font-size: 46px; }

  /* Top panel */
  .top-panel {
    position: absolute; left: 270px; top: 80px; width: 870px; height: 500px;
    background: var(--cream); overflow: hidden;
  }
  .floral-pattern {
    position: absolute; inset: 0;
    background: radial-gradient(ellipse at 70% 30%, var(--pattern-mid) 0%, var(--pattern-light) 45%, var(--cream) 85%);
    opacity: .8;
  }
  .silhouette {
    position: absolute; background: var(--deep-green);
    border-radius: 50% 45% 40% 50%;
  }
  .top-panel .silhouette { left: 60px; top: 90px; width: 270px; height: 330px; }

  .label {
    position: absolute; left: 330px; top: 60px; width: 470px; height: 300px;
    background: var(--leaf-green);
    border: 3px solid var(--cream); outline: 2px solid var(--deep-green); outline-offset: -10px;
    text-align: center; padding-top: 30px;
  }
  .brand-name {
    font-family: "Cinzel", serif; font-weight: 700; color: var(--ink-green);
    letter-spacing: 2px; line-height: 1;
  }
  .label .brand-name { font-size: 56px; }
  .claim-band {
    margin: 26px 0 18px; background: var(--band-green); color: var(--white);
    font-family: "Cinzel", serif; font-weight: 500; font-size: 22px; line-height: 1.25; padding: 10px 0;
  }
  .natural-note { font-family: "Cinzel", serif; font-weight: 700; font-size: 24px; color: var(--ink-green); }
  .net-weight {
    position: absolute; left: 600px; top: 395px;
    font-family: "Cinzel", serif; font-weight: 700; font-size: 22px; color: var(--ink-green);
  }

  /* Front panel */
  .front-panel {
    position: absolute; left: 270px; top: 600px; width: 870px; height: 250px;
    background: linear-gradient(90deg, var(--lime), var(--leaf-green));
    overflow: hidden;
  }
  .front-panel .silhouette { left: 70px; top: 45px; width: 140px; height: 170px; }
  .front-copy { position: absolute; left: 270px; top: 30px; width: 560px; text-align: center; }
  .front-copy .brand-name { font-size: 48px; margin-bottom: 14px; }
  .front-copy p { font-family: "Tinos", serif; font-size: 22px; color: var(--ink-green); line-height: 1.25; }
</style>
</head>
<body>
<main class="canvas">

  <section class="end-panel">
    <span class="brand-name">KIRO Soap</span>
  </section>

  <section class="top-panel">
    <div class="floral-pattern" role="img" aria-label="Engraved green floral and leaf pattern"></div>
    <div class="silhouette" role="img" aria-label="Dark green woman profile silhouette with leafy swirls"></div>
    <div class="label">
      <div class="brand-name">KIRO Soap</div>
      <div class="claim-band">Very effective for<br>Acne &amp; Skin irritation</div>
      <div class="natural-note">100% Natural</div>
    </div>
    <div class="net-weight">Net Wt.: 100 Gms</div>
  </section>

  <section class="front-panel">
    <div class="silhouette" role="img" aria-label="Small woman profile silhouette with leafy swirls"></div>
    <div class="front-copy">
      <div class="brand-name">KIRO Soap</div>
      <p>100% natural.</p>
      <p>Made from nature Tropic oil.</p>
      <p>Very effective for Acne &amp; Skin irritation</p>
      <p>Use for all skin types including sensitive skin</p>
    </div>
  </section>

</main>
</body>
</html>
```